wordpress website Carla Winfield, Author, Speaker and Coach

Need a wordpress blogging website for author/speaker/coach.
I have paid for hosting on nestparrot.
I am currently writing a book - Launchpad to Campus - Steps and strategies to prepare you to thrive in college and beyond. Eventually, I will have an Academic/Life Coaching program targeting high school and college students. This website's purpose is to build my email list. I can offer the following reports as incentive for email sign-up:
1. Six Habits That Get Your Teen Through University On Schedule and Debt-Light
2. Surprising Routes to Fund Your Degree
3. SAT/ACT vocabulary word of the day

facebook page: https://www.facebook.com/Carla-Winfield-AcademicLife-Coach-918273645501928/

I would like to have these pages:

1. Home or About page

High school is becoming more and more stressful for students. Not only are they taking more AP classes than ever before, and often spending $1,000’s on SAT/ACT prep programs, most are NOT prepared for success in college. Only 19% of students are graduating from college within 4 years and only 56% are graduating within 6 years. With the cost of higher education skyrocketing, each extra year of school can costs families $40,000 - $60,000 when you factor in living expenses. Then, when students do graduate, they are often underemployed.

Carla's approach is whole person oriented. Her programs help students learn life skills in addition to the study, time management skills, etc. offered by most academic coaching programs. Our program addresses all of the major causes of failure to graduate within 4 years, and is based on sound educational research. Carla's program initially provides the daily interaction needed to successfully change behaviors and seat new success habits, unlike many programs in which students interact with coaches only once a week.
Bio
Carla Winfield is a certified teacher and holds advanced certification in academic coaching and tutoring. She also is a certified trainer in the Morris Tellwright Achievement Keys. She has three successful adult children, and helped them overcome learning differences and thrive.

2. Blog

3. Contact - Include form (I split time between USA and Saudi Arabia, so I will call or email people back, but don't want to leave a phone number)
info@carlawinfield.example

4. Store – 1 book for now
Launchpad to Campus
Steps and strategies to prepare you to thrive in college and beyond
Available 12/01/2017
I could make a preview chapter available for download

5. Speaking
Carla Winfield is available for keynote addresses and half-day, full day or multi-day workshops. I will develop details later

6.Coaching programs
I will develop details later

Target Market(s)

high school students who are college bound and their parents

Number of Pages Required

5+ page

Font styles to use
Sans Serif

Colors

Designer to choose colors to be used in the design.

Requirements
Nice to have
• integration with post finch for contact management

```html
<!DOCTYPE html>
<html lang="en">
<head>
<meta charset="utf-8">
<title>Carla Winfield — Author, Speaker and Coach</title>
<link href="https://fonts.googleapis.com/css2?family=Mulish:ital,wght@0,300;0,400;0,600;0,700;1,400&display=swap" rel="stylesheet">
<style>
:root{
  --green:#0f8a44;
  --green-dark:#0a6f36;
  --green-bright:#3fb84b;
  --purple:#8884c6;
  --purple-soft:#aaa5d8;
  --ink:#2b2b2b;
  --muted:#8a8a8a;
  --grey-bg:#eeeeee;
  --white:#ffffff;
  --hero-dark:#3b3a37;
}
*{margin:0;padding:0;box-sizing:border-box}
html,body{width:1200px;height:2922px;overflow:hidden}
body{position:relative;font-family:'Mulish',sans-serif;color:var(--ink);background:var(--white)}
.abs{position:absolute}
a{color:inherit;text-decoration:none}

/* header */
.site-header{left:0;top:0;width:1200px;height:90px;background:var(--white);z-index:5}
.brand{left:129px;top:20px;display:flex;align-items:center;gap:12px}
.brand-dot{width:48px;height:48px;border-radius:50%;background:var(--green)}
.brand-name{font-size:32px;font-weight:400;color:var(--green)}
.main-nav{right:128px;top:34px;display:flex;gap:36px;font-size:17px;color:#8a8a8a}
.main-nav .current{color:var(--green);font-weight:600}

/* hero */
.hero{left:0;top:90px;width:1200px;height:560px;background:linear-gradient(100deg,#4a4641 0%,#3c3934 45%,#2f2d2a 100%)}
.hero-photo{left:0;top:0;width:1200px;height:560px;background:linear-gradient(180deg,rgba(110,100,88,.35) 0%,rgba(60,56,50,.1) 40%,rgba(120,110,95,.25) 100%)}
.hero-title{left:168px;top:296px;font-size:37px;font-weight:400;color:var(--white);letter-spacing:.5px}
.hero-sub{left:168px;top:352px;font-size:16px;line-height:24px;color:var(--white);text-transform:uppercase}
.btn-pill{left:168px;top:417px;width:121px;height:32px;border-radius:16px;background:var(--green);color:var(--white);font-size:12px;font-weight:700;display:flex;align-items:center;justify-content:center}
.hero-arrow{top:318px;z-index:4}
.book-cover{left:706px;top:196px;width:270px;height:352px;background:linear-gradient(180deg,#8c98a3 0%,#7d8a82 50%,#148a46 70%,#0e7a3c 100%);box-shadow:8px 0 0 #e9e9e9,10px 6px 18px rgba(0,0,0,.5)}

/* bio */
.bio{left:0;top:640px;width:1200px;height:362px;background:linear-gradient(160deg,#139049 0%,#0e8441 60%,#0b7a3a 100%)}
.hero-curve{left:0;top:570px;z-index:3}
.bio-photo{left:189px;top:740px;width:188px;height:188px;border-radius:50%;background:radial-gradient(circle at 50% 45%,#b88a72 0%,#8c5f4c 55%,#3a2a24 100%);border:4px solid #2a2a2a;z-index:4}
.bio-title{left:406px;top:756px;font-size:23px;color:var(--white);font-weight:400;z-index:4}
.bio-text{left:406px;top:790px;width:640px;font-size:14px;line-height:22px;color:#e6f3ea;z-index:4}
.btn-ghost-sm{left:406px;top:876px;width:106px;height:29px;border:1.5px solid rgba(255,255,255,.8);border-radius:15px;color:var(--white);font-size:11px;display:flex;align-items:center;justify-content:center;z-index:4}

/* coaching */
.coaching{left:0;top:998px;width:1200px;height:447px;background:linear-gradient(110deg,#0d7a3b 0%,#129248 55%,#1a9a4e 100%)}
.coaching-photo{left:0;top:0}
.coaching-title{left:133px;top:1082px;font-size:33px;color:var(--white);font-weight:400}
.coaching-text{left:133px;top:1140px;width:470px;font-size:14.5px;line-height:22.5px;color:#e9f4ec}
.btn-ghost{left:134px;top:1300px;width:146px;height:46px;border:2px solid var(--white);color:var(--white);font-size:14px;display:flex;align-items:center;justify-content:center}

/* feature cards */
.card{top:1558px;width:462px;height:243px;border:2px solid var(--purple);background:var(--white);text-align:center}
.card-book{left:109px}
.card-speaking{left:590px;border-color:var(--green)}
.card-icon{top:-53px;left:178px;width:104px;height:104px;border-radius:50%;background:var(--white);border:2px solid var(--purple);display:flex;align-items:center;justify-content:center}
.card-speaking .card-icon{border-color:var(--green)}
.card-kicker{left:0;width:100%;top:74px;font-size:18px;color:var(--purple)}
.card-title{left:0;width:100%;top:100px;font-size:24px;color:var(--purple)}
.card-speaking .card-title{top:76px;color:var(--green);font-weight:600}
.card-text{left:60px;width:342px;top:140px;font-size:13px;line-height:24px;color:var(--muted)}
.card-speaking .card-text{top:108px;left:34px;width:394px}
.card-btn{top:1780px;z-index:2}

/* blog */
.blog{left:0;top:1903px;width:1200px;height:500px;background:var(--grey-bg)}
.blog-heading{left:0;width:1200px;top:1966px;text-align:center;font-size:29px;font-weight:400;color:#2a2a2a}
.post{top:2056px;width:471px;height:244px;background:var(--white);box-shadow:0 2px 6px rgba(0,0,0,.08)}
.post-1{left:109px}
.post-2{left:616px}
.post-image{left:0;top:0;width:212px;height:244px}
.post-1 .post-image{background:linear-gradient(135deg,#9b6b4a 0%,#c7a07e 50%,#6a5040 100%)}
.post-2 .post-image{background:linear-gradient(135deg,#6f6a4e 0%,#a59a78 45%,#3e4a6a 100%)}
.post-body{left:232px;top:20px;width:225px}
.post-title{font-size:15.5px;line-height:20px;color:#2b2b2b;font-weight:400}
.post-date{margin-top:12px;font-size:12.5px;font-style:italic;color:var(--green)}
.post-excerpt{margin-top:10px;font-size:11.5px;line-height:16px;color:#555}
.post-more{margin-top:14px;font-size:12px;color:#333}

/* newsletter */
.newsletter{left:0;top:2380px;width:1200px;height:372px;background:linear-gradient(180deg,#b4aedd 0%,#a49ed4 50%,#b7b1e0 100%)}
.newsletter-wave{left:0;top:2360px;z-index:2}
.newsletter-title{left:0;width:1200px;top:2460px;text-align:center;font-size:30px;line-height:34px;color:var(--white);font-weight:400;text-transform:uppercase;letter-spacing:.5px;z-index:3}
.newsletter-sub{left:0;width:1200px;top:2538px;text-align:center;font-size:17px;color:#eeecf8;z-index:3}
.field{top:2597px;height:43px;background:var(--white);font-size:15px;color:#aaa;padding:0 16px;display:flex;align-items:center;z-index:3}
.field-name{left:234px;width:274px}
.field-email{left:512px;width:277px}
.btn-subscribe{left:793px;top:2597px;width:150px;height:43px;border:2px solid var(--white);color:var(--white);font-size:15px;display:flex;align-items:center;justify-content:center;z-index:3}

/* footer */
.site-footer{left:0;top:2752px;width:1200px;height:170px;background:var(--white)}
.badge{left:151px;top:2795px;width:100px;height:100px;border-radius:50%;background:radial-gradient(circle,#e6e6e6 0%,#bdbdbd 70%,#9c9c9c 100%)}
.footer-nav{left:287px;top:2798px;display:flex;gap:24px;font-size:13.5px;color:#333}
.copyright{left:287px;top:2828px;font-size:12.5px;color:#9a9a9a}
.social{left:922px;top:2804px;display:flex;gap:7px}
.social span{width:34px;height:34px;border:2px solid var(--green-bright)}
</style>
</head>
<body>

<header class="site-header abs">
  <a class="brand abs" href="#"><span class="brand-dot"></span><span class="brand-name">Carla Winfield</span></a>
  <nav class="main-nav abs">
    <a class="current" href="#">Home</a><a href="#">Blog</a><a href="#">Store</a><a href="#">Speaking</a><a href="#">Coaching Program</a><a href="#">Contact</a>
  </nav>
</header>

<section class="hero abs">
  <div class="hero-photo abs" role="img" aria-label="Photo of a student on a beach at dusk"></div>
</section>
<svg class="hero-arrow abs" style="left:74px" width="30" height="60" viewBox="0 0 30 60"><path d="M26 4 L4 30 L26 56" fill="none" stroke="#fff" stroke-width="2"/></svg>
<svg class="hero-arrow abs" style="left:1106px" width="30" height="60" viewBox="0 0 30 60"><path d="M4 4 L26 30 L4 56" fill="none" stroke="#fff" stroke-width="2"/></svg>
<h1 class="hero-title abs">LAUNCHPAD TO CAMPUS</h1>
<p class="hero-sub abs">Steps and strategies to prepare you to<br>thrive in college and beyond</p>
<a class="btn-pill abs" href="#">READ MORE</a>
<div class="book-cover abs" role="img" aria-label="Cover of the book Launchpad to Campus showing a university building and a student"></div>

<section class="bio abs"></section>
<svg class="hero-curve abs" width="1200" height="80" viewBox="0 0 1200 80"><path d="M0 15 Q600 135 1200 15 L1200 80 L0 80Z" fill="#139049"/></svg>
<div class="bio-photo abs" role="img" aria-label="Portrait photo of Carla Winfield"></div>
<h2 class="bio-title abs">BIO</h2>
<p class="bio-text abs">Carla Winfield is a certified teacher and holds advanced certification in academic coaching and tutoring. She also is a certified trainer in the Morris Tellwright Achievement Keys. She has three successful adult children, and helped them overcome learning differences and thrive.</p>
<a class="btn-ghost-sm abs" href="#">READ MORE »</a>

<section class="coaching abs">
  <svg class="coaching-photo abs" width="1200" height="447" viewBox="0 0 1200 447" role="img" aria-label="Photo of a dandelion seed head releasing seeds">
    <defs>
      <radialGradient id="seedhead" cx="72%" cy="38%" r="45%">
        <stop offset="0" stop-color="#eef3ee"/>
        <stop offset=".35" stop-color="#b9d7bf"/>
        <stop offset="1" stop-color="#0f7f3d"/>
      </radialGradient>
    </defs>
    <polygon points="645,0 1200,0 1200,447 536,447" fill="url(#seedhead)"/>
  </svg>
</section>
<h2 class="coaching-title abs">Coaching Program</h2>
<p class="coaching-text abs">Carla's approach is whole person oriented. Her programs help students learn life skills in addition to the study, time management skills, etc. offered by most academic coaching programs. Our program addresses all of the major causes of failure to graduate within 4 years, and is based on sound educational research. Carla's program initially provides the dailyinteraction needed to successfully change behaviors</p>
<a class="btn-ghost abs" href="#">READ MORE</a>

<article class="card card-book abs">
  <div class="card-icon abs">
    <svg width="50" height="40" viewBox="0 0 50 40"><path d="M25 8 C18 3 8 3 3 5 V35 C8 33 18 33 25 37 C32 33 42 33 47 35 V5 C42 3 32 3 25 8Z M25 8 V37" fill="none" stroke="#8884c6" stroke-width="2.2" stroke-linejoin="round"/></svg>
  </div>
  <p class="card-kicker abs">My Book</p>
  <h3 class="card-title abs">Launchpad to Campus</h3>
  <p class="card-text abs">Steps and strategies to prepare you to thrive in college and beyond</p>
</article>
<svg class="card-btn abs" style="left:246px" width="182" height="44" viewBox="0 0 182 44"><polygon points="16,0 166,0 182,22 166,44 16,44 0,22" fill="#8884c6"/><text x="91" y="28" text-anchor="middle" font-family="Mulish, sans-serif" font-size="15" fill="#fff">READ MORE</text></svg>

<article class="card card-speaking abs">
  <div class="card-icon abs">
    <svg width="50" height="44" viewBox="0 0 50 44"><path d="M6 16 H14 L38 4 V40 L14 28 H6Z M14 16 V28 M18 28 L22 40 H28 L25 30 M42 14 C46 18 46 26 42 30" fill="none" stroke="#0f8a44" stroke-width="2.2" stroke-linejoin="round"/></svg>
  </div>
  <h3 class="card-title abs">Speaking</h3>
  <p class="card-text abs">Praesent elementum elit at tellus nec ultricies sit amet porttitor mattis enim in massa libero interdum nec interdum vel blandit sed nulla in ullamcorper est eget tempor cursus neque mi</p>
</article>
<svg class="card-btn abs" style="left:730px" width="182" height="44" viewBox="0 0 182 44"><polygon points="16,0 166,0 182,22 166,44 16,44 0,22" fill="#3fb84b"/><text x="91" y="28" text-anchor="middle" font-family="Mulish, sans-serif" font-size="15" fill="#fff">READ MORE</text></svg>

<section class="blog abs"></section>
<h2 class="blog-heading abs">LATEST BLOG</h2>
<article class="post post-1 abs">
  <div class="post-image abs" role="img" aria-label="Photo of two smiling students holding books"></div>
  <div class="post-body abs">
    <h3 class="post-title">Sed ut perspiciatis unde omnis natus error sit voluptatem</h3>
    <p class="post-date">SEP 19, 2017</p>
    <p class="post-excerpt">Sed ut perspiciatis unde omnis iste natus voluptatem accusantium doloremque laudantium, totam rem aperiam, eaque ipsa quae ab illo inventore veritatis et quasi architecto beatae vitae dicta</p>
    <p class="post-more">Read More +</p>
  </div>
</article>
<article class="post post-2 abs">
  <div class="post-image abs" role="img" aria-label="Photo of a student studying with a laptop on a window ledge"></div>
  <div class="post-body abs">
    <h3 class="post-title">Sed ut perspiciatis unde omnis natus error sit voluptatem</h3>
    <p class="post-date">SEP 19, 2017</p>
    <p class="post-excerpt">Sed ut perspiciatis unde omnis iste natus voluptatem accusantium doloremque laudantium, totam rem aperiam, eaque ipsa quae ab illo inventore veritatis et quasi architecto beatae vitae dicta</p>
    <p class="post-more">Read More +</p>
  </div>
</article>

<section class="newsletter abs" role="img" aria-label="Photo of students jumping against the sky, tinted lavender"></section>
<svg class="newsletter-wave abs" width="1200" height="60" viewBox="0 0 1200 60"><path d="M0 0 H1200 V30 Q900 0 600 30 Q300 58 0 32Z" fill="#eeeeee"/></svg>
<h2 class="newsletter-title abs">Sign up for our newsletter and<br>get the free report</h2>
<p class="newsletter-sub abs">Six Habits That Get Your Teen Through University On Schedule and Debt-Light</p>
<div class="field field-name abs">Name</div>
<div class="field field-email abs">Email address</div>
<a class="btn-subscribe abs" href="#">SUBSCRIBE</a>

<footer class="site-footer abs"></footer>
<div class="badge abs" role="img" aria-label="Certified trainer badge"></div>
<nav class="footer-nav abs"><a href="#">Home</a><a href="#">Blog</a><a href="#">Store</a><a href="#">Speaking</a><a href="#">Coaching Program</a><a href="#">Contact</a></nav>
<p class="copyright abs">© 2017 Company Name &nbsp;All right reserved</p>
<div class="social abs" aria-label="Social links"><span></span><span></span><span></span><span></span></div>

</body>
</html>
```